We want to a home page of our company in Tradovex.com

We sell both home textile and hotel linen, but we are more professional on hotel linen , we want to make this page to be a very global style that is in the line of buyers reading habits , we want to show them that we are very professional on this business line, and the page must be very elegant and stylish
our current page is https://qelmarito.en.tradovex.com/?spm=a2700.shop_cp.88.16 which i dont like , we want to make it international style and colors not so shine but very north euro feeling and logical is very clear
You could select photos from outside
We have a lot of photos, if you need more photos you pls contact us
Europe/North America / Israel / South East Asia etc
1 page
- MY BRAND LOGO

```html
<!DOCTYPE html>
<html lang="en">
<head>
<meta charset="utf-8">
<title>Qelmarito Hotel Linen</title>
<link href="https://fonts.googleapis.com/css2?family=Bowlby+One&family=Roboto:ital,wght@0,400;0,500;0,700;1,400&display=swap" rel="stylesheet">
<style>
:root{
  --orange:#ec6a2a;
  --orange-dark:#d85a1c;
  --ink:#2f2f2f;
  --text:#555;
  --muted:#8a8a8a;
  --dark:#333333;
  --darker:#2b2b2b;
  --line:#e3e3e3;
  --panel:#f4f4f4;
  --white:#ffffff;
}
*{box-sizing:border-box;margin:0;padding:0}
html,body{width:1200px;height:3838px;overflow:hidden}
body{position:relative;font-family:"Roboto",Arial,sans-serif;color:var(--ink);background:var(--white)}
.abs{position:absolute}
a{color:inherit;text-decoration:none}

/* header */
.topbar{left:0;top:0;width:1200px;height:83px;background:var(--dark)}
.brand{left:143px;top:18px;font-weight:700;font-size:40px;color:var(--white);letter-spacing:1px;display:flex;align-items:center;gap:10px}
.brand .dot{width:14px;height:14px;border-radius:50%;background:var(--white)}
.search{left:432px;top:21px;width:403px;height:42px;background:var(--white);border-radius:21px;font-size:11px;color:#777;padding:14px 20px}
.search .go{position:absolute;right:6px;top:6px;width:30px;height:30px;border-radius:50%;background:var(--dark)}
.account{left:860px;top:33px;font-size:13px;color:var(--white);display:flex;gap:8px;align-items:center}
.account .ic{color:var(--orange)}
.navbar{left:0;top:83px;width:1200px;height:41px;background:var(--orange)}
.nav{left:143px;top:83px;height:41px;display:flex;font-size:13px;font-weight:500;color:var(--white)}
.nav a{padding:0 16px;line-height:41px}
.nav a.active{background:var(--dark)}
.currency{left:988px;top:96px;font-size:13px;color:var(--white);display:flex;align-items:center;gap:6px}
.currency .flag{width:16px;height:16px;border-radius:50%;background:#5a6fb0}

/* hero */
.categories{left:143px;top:140px;width:246px;height:483px;background:var(--panel);border:1px solid var(--line)}
.categories h3{position:absolute;left:44px;top:18px;font-size:21px;font-weight:700}
.cat{position:absolute;left:44px;display:flex;align-items:center;gap:24px;font-size:12px;font-weight:500}
.hex{width:66px;height:76px;clip-path:polygon(50% 0,100% 25%,100% 75%,50% 100%,0 75%,0 25%)}
.slider{left:400px;top:140px;width:655px;height:483px;background:linear-gradient(135deg,#243a63 0%,#2f4c7c 45%,#c9ccd6 75%,#aeb3bf 100%)}
.slide-title{left:514px;top:248px;font-family:"Bowlby One",sans-serif;font-size:54px;line-height:72px;color:var(--orange)}
.slide-sub{left:517px;top:402px;font-size:25px;font-weight:500;color:var(--white)}
.btn{background:var(--orange);color:var(--white);font-weight:700;text-align:center;display:block}
.shop{left:519px;top:462px;width:128px;height:40px;line-height:40px;font-size:13px}
.arrow{width:20px;height:30px}

/* section headings */
.section-title{font-family:"Bowlby One",sans-serif;color:var(--orange);font-size:44px;line-height:50px;white-space:nowrap}
.rule{height:6px;background:var(--line)}

/* products */
.product{width:219px;text-align:center}
.product .photo{height:155px;position:relative;border:1px solid var(--line)}
.play{position:absolute;left:50%;top:50%;width:36px;height:36px;margin:-18px 0 0 -18px}
.product h4{margin-top:26px;font-size:16px;font-weight:500}
.product .price{margin-top:12px;font-size:10px;font-style:italic;color:var(--muted)}
.product .btn{margin:17px auto 0;width:95px;height:28px;line-height:28px;font-size:9px}

/* about */
.about{left:143px;top:1502px;width:624px;height:413px;border:1px solid var(--line)}
.frame{left:847px;top:1673px;width:262px;height:270px;border:3px solid var(--orange)}
.video{left:596px;top:1550px;width:459px;height:316px;background:linear-gradient(160deg,#9a9ea6 0%,#c7cbd1 40%,#eceef0 70%,#b5b8bd 100%)}
.about-title{left:183px;top:1546px}
.about-text{left:185px;top:1620px;width:380px;font-size:13px;line-height:25.5px;color:var(--text)}
.readmore{left:185px;top:1821px;width:128px;height:40px;line-height:40px;font-size:13px}

/* popular */
.pop{width:219px;height:249px;border:1px solid #d8d8d8}
.pop .photo{height:155px}
.pop h4{margin:26px 0 0 10px;font-size:16px;font-weight:500}
.pop p{margin:12px 0 0 10px;font-size:10px;font-style:italic;color:var(--muted);line-height:16px}

/* brands */
.brand-row{left:150px;top:2630px;width:900px;display:flex;justify-content:space-between;align-items:center}
.partner{font-size:21px;font-weight:500;color:#4a4a4a}
.circle-btn{width:28px;height:28px;border-radius:50%;border:1px solid #999;display:flex;align-items:center;justify-content:center}

/* testimonials */
.quote{width:299px;height:143px;border:1px solid var(--line);padding:20px 16px}
.quote p{font-size:11px;font-style:italic;line-height:19px;color:var(--text)}
.quote .who{margin-top:10px;font-size:13px;font-weight:500;color:var(--orange)}
.avatar{width:82px;height:94px}
.stars{display:flex;gap:5px}

/* newsletter & footer */
.newsletter{left:0;top:3189px;width:1200px;height:649px;background:var(--dark)}
.news-title{left:0;top:3263px;width:1200px;text-align:center}
.news-text{left:0;top:3356px;width:1200px;text-align:center;font-size:15px;color:var(--white)}
.email{left:322px;top:3423px;width:554px;height:44px;background:var(--white);border-radius:22px;font-size:13px;padding:15px 26px;color:#444}
.subscribe{left:748px;top:3425px;width:126px;height:40px;line-height:40px;border-radius:20px;font-size:14px}
.divider{left:0;top:3528px;width:1200px;height:1px;background:#444}
.pay{left:398px;top:3592px;display:flex;gap:9px}
.pay span{width:34px;height:22px;border-radius:3px;background:#d7d9de}
.social{left:643px;top:3587px;display:flex;gap:10px}
.social span{width:33px;height:33px;border-radius:50%;background:var(--white)}
.footer-nav{left:0;top:3658px;width:1200px;text-align:center;font-size:15px;font-weight:500;color:var(--white);word-spacing:6px}
.copy{left:0;top:3702px;width:1200px;text-align:center;font-size:11px;color:#ddd}
.foot-brand{left:0;top:3757px;width:1200px;text-align:center;font-size:40px;font-weight:700;color:var(--white)}
</style>
</head>
<body>

<!-- header -->
<div class="abs topbar"></div>
<div class="abs brand"><span>Qelmarito</span><span class="dot"></span></div>
<div class="abs search">Search Products<span class="go"><svg width="30" height="30" viewBox="0 0 30 30"><circle cx="14" cy="14" r="5" fill="none" stroke="#fff" stroke-width="2"/><path d="M18 18l4 4" stroke="#fff" stroke-width="2"/></svg></span></div>
<div class="abs account"><span class="ic">&#9679;</span><span>Sign In&nbsp; Join Free</span><span>|</span><span class="ic">&#9632;</span><span>Cart(0)</span></div>
<div class="abs navbar"></div>
<nav class="abs nav">
  <a class="active">HOME</a><a>PRODUCTS</a><a>PROFILE</a><a>CONTACTS</a><a>VIDEO</a><a>PROMOTION</a><a>FEEDS</a><a>VIEW MORE</a>
</nav>
<div class="abs currency"><span class="flag"></span>USD <svg width="10" height="6"><path d="M0 0h10L5 6z" fill="#fff"/></svg></div>

<!-- hero -->
<aside class="abs categories">
  <h3>CATEGORIES</h3>
  <div class="cat" style="top:63px"><div class="hex" role="img" aria-label="Bathrobe photo" style="background:linear-gradient(#d8d6d3,#a9a6a2)"></div>BATHROBE</div>
  <div class="cat" style="top:144px"><div class="hex" role="img" aria-label="Towel photo" style="background:linear-gradient(#e9c4b5,#c99886)"></div>TOWEL</div>
  <div class="cat" style="top:224px"><div class="hex" role="img" aria-label="Pillow photo" style="background:linear-gradient(#8f9397,#dcdcdc)"></div>PILLOW</div>
  <div class="cat" style="top:303px"><div class="hex" role="img" aria-label="F&amp;B linen photo" style="background:linear-gradient(#5a1a22,#2c1b1c)"></div>F&amp;B LINEN</div>
  <div class="cat" style="top:385px"><div class="hex" role="img" aria-label="Bedding photo" style="background:linear-gradient(#4a3a34,#e5e2de)"></div>BEDDING</div>
</aside>
<div class="abs slider" role="img" aria-label="Hotel bedroom with white bedding against a navy wall"></div>
<div class="abs slide-title">BEST QUALITY<br>HOTEL LINEN</div>
<div class="abs slide-sub">Guest Room Bedding</div>
<a class="abs btn shop">SHOP NOW</a>
<svg class="abs arrow" style="left:426px;top:366px" viewBox="0 0 20 30"><path d="M14 6L6 15l8 9" fill="none" stroke="#fff" stroke-width="3"/></svg>
<svg class="abs arrow" style="left:1009px;top:366px" viewBox="0 0 20 30"><path d="M6 6l8 9-8 9" fill="none" stroke="#fff" stroke-width="3"/></svg>

<!-- featured -->
<h2 class="abs section-title" style="left:141px;top:695px">FEATURED PRODUCTS</h2>
<div class="abs rule" style="left:666px;top:717px;width:389px"></div>

<section>
  <div class="abs product" style="left:143px;top:809px"><div class="photo" role="img" aria-label="Hotel bed with grey trim" style="background:linear-gradient(135deg,#6b5b52,#d9d7d3)"><svg class="play" viewBox="0 0 36 36"><circle cx="18" cy="18" r="16" fill="none" stroke="#fff" stroke-width="2"/><path d="M14 11l11 7-11 7z" fill="#fff"/></svg></div><h4>PRODUCT NAME</h4><div class="price">$28.00 - $56.00/Set 10.0 Sets(Min. Order)</div><a class="btn">VIEW MORE</a></div>
  <div class="abs product" style="left:374px;top:809px"><div class="photo" role="img" aria-label="White hotel bed set" style="background:linear-gradient(135deg,#b7b4ae,#ecebe8)"><svg class="play" viewBox="0 0 36 36"><circle cx="18" cy="18" r="16" fill="none" stroke="#fff" stroke-width="2"/><path d="M14 11l11 7-11 7z" fill="#fff"/></svg></div><h4>PRODUCT NAME</h4><div class="price">$28.00 - $56.00/Set 10.0 Sets(Min. Order)</div><a class="btn">VIEW MORE</a></div>
  <div class="abs product" style="left:605px;top:809px"><div class="photo" role="img" aria-label="Bed set with dark stripe" style="background:linear-gradient(135deg,#8c8c8c,#dedede)"><svg class="play" viewBox="0 0 36 36"><circle cx="18" cy="18" r="16" fill="none" stroke="#fff" stroke-width="2"/><path d="M14 11l11 7-11 7z" fill="#fff"/></svg></div><h4>PRODUCT NAME</h4><div class="price">$28.00 - $56.00/Set 10.0 Sets(Min. Order)</div><a class="btn">VIEW MORE</a></div>
  <div class="abs product" style="left:836px;top:809px"><div class="photo" role="img" aria-label="Bed set with brown accents" style="background:linear-gradient(135deg,#6d5c55,#cfc9c4)"><svg class="play" viewBox="0 0 36 36"><circle cx="18" cy="18" r="16" fill="none" stroke="#fff" stroke-width="2"/><path d="M14 11l11 7-11 7z" fill="#fff"/></svg></div><h4>PRODUCT NAME</h4><div class="price">$28.00 - $56.00/Set 10.0 Sets(Min. Order)</div><a class="btn">VIEW MORE</a></div>

  <div class="abs product" style="left:143px;top:1121px"><div class="photo" role="img" aria-label="White bed with navy runner" style="background:linear-gradient(135deg,#5e6f86,#e6e8ec)"><svg class="play" viewBox="0 0 36 36"><circle cx="18" cy="18" r="16" fill="none" stroke="#fff" stroke-width="2"/><path d="M14 11l11 7-11 7z" fill="#fff"/></svg></div><h4>PRODUCT NAME</h4><div class="price">$28.00 - $56.00/Set 10.0 Sets(Min. Order)</div><a class="btn">VIEW MORE</a></div>
  <div class="abs product" style="left:374px;top:1121px"><div class="photo" role="img" aria-label="Pillowcase with grey band" style="background:linear-gradient(135deg,#a3a3a3,#f0f0f0)"><svg class="play" viewBox="0 0 36 36"><circle cx="18" cy="18" r="16" fill="none" stroke="#fff" stroke-width="2"/><path d="M14 11l11 7-11 7z" fill="#fff"/></svg></div><h4>PRODUCT NAME</h4><div class="price">$28.00 - $56.00/Set 10.0 Sets(Min. Order)</div><a class="btn">VIEW MORE</a></div>
  <div class="abs product" style="left:605px;top:1121px"><div class="photo" role="img" aria-label="Bed set with purple piping" style="background:linear-gradient(135deg,#7b7b80,#dadada)"><svg class="play" viewBox="0 0 36 36"><circle cx="18" cy="18" r="16" fill="none" stroke="#fff" stroke-width="2"/><path d="M14 11l11 7-11 7z" fill="#fff"/></svg></div><h4>PRODUCT NAME</h4><div class="price">$28.00 - $56.00/Set 10.0 Sets(Min. Order)</div><a class="btn">VIEW MORE</a></div>
  <div class="abs product" style="left:836px;top:1121px"><div class="photo" role="img" aria-label="Bed set with red trim" style="background:linear-gradient(135deg,#a18a8e,#e2dede)"><svg class="play" viewBox="0 0 36 36"><circle cx="18" cy="18" r="16" fill="none" stroke="#fff" stroke-width="2"/><path d="M14 11l11 7-11 7z" fill="#fff"/></svg></div><h4>PRODUCT NAME</h4><div class="price">$28.00 - $56.00/Set 10.0 Sets(Min. Order)</div><a class="btn">VIEW MORE</a></div>
</section>

<!-- about -->
<div class="abs about"></div>
<div class="abs frame"></div>
<div class="abs video" role="img" aria-label="Textile factory floor with linen on cutting tables"><svg class="play" style="width:54px;height:54px;margin:-27px 0 0 -27px" viewBox="0 0 36 36"><circle cx="18" cy="18" r="16" fill="none" stroke="#fff" stroke-width="2"/><path d="M14 11l11 7-11 7z" fill="#fff"/></svg></div>
<h2 class="abs section-title about-title">ABOUT US</h2>
<p class="abs about-text">Harrowgate Qelmarito Textile Co.,Ltd. was established on 2013, is a professional linen solution provider,devotes into whole range of hotel bed linen, bath linen and F&amp;B linen.We are much more concerned about products quality, services with our the best sincerity to meet different kind of requirements from markets all over the worldThe typical international hotel brands we ever cooperated are</p>
<a class="abs btn readmore">READ MORE</a>

<!-- most popular -->
<h2 class="abs section-title" style="left:141px;top:2057px">MOST POPULAR</h2>
<div class="abs rule" style="left:530px;top:2079px;width:525px"></div>
<div class="abs pop" style="left:143px;top:2171px"><div class="photo" role="img" aria-label="Bed with red runner and patterned cushions" style="background:linear-gradient(160deg,#77797d,#e8e8e8 60%,#b33a3f)"></div><h4>PRODUCT NAME</h4><p>$28.00 - $56.00/Set 10.0 Sets<br>(Min. Order)</p></div>
<div class="abs pop" style="left:374px;top:2171px"><div class="photo" role="img" aria-label="Bed with gold throw" style="background:linear-gradient(160deg,#c9c7c3,#efeeec 60%,#b88a2c)"></div><h4>PRODUCT NAME</h4><p>$28.00 - $56.00/Set 10.0 Sets<br>(Min. Order)</p></div>
<div class="abs pop" style="left:605px;top:2171px"><div class="photo" role="img" aria-label="Bed with wooden headboard in dark room" style="background:linear-gradient(160deg,#3a4044,#7a5a44 50%,#e4e2df)"></div><h4>PRODUCT NAME</h4><p>$28.00 - $56.00/Set 10.0 Sets<br>(Min. Order)</p></div>
<div class="abs pop" style="left:836px;top:2171px"><div class="photo" role="img" aria-label="Pink bedding in dark room" style="background:linear-gradient(160deg,#2e2e30,#b7a3a6 55%,#d9c9cb)"></div><h4>PRODUCT NAME</h4><p>$28.00 - $56.00/Set 10.0 Sets<br>(Min. Order)</p></div>

<!-- brands -->
<h2 class="abs section-title" style="left:141px;top:2517px">OUR BRANDS</h2>
<div class="abs rule" style="left:474px;top:2539px;width:581px"></div>
<div class="abs circle-btn" style="left:90px;top:2641px"><svg width="10" height="12"><path d="M7 1L2 6l5 5" fill="none" stroke="#777" stroke-width="1.5"/></svg></div>
<div class="abs circle-btn" style="left:1081px;top:2641px"><svg width="10" height="12"><path d="M3 1l5 5-5 5" fill="none" stroke="#777" stroke-width="1.5"/></svg></div>
<div class="abs brand-row">
  <span class="partner">Halvorn</span><span class="partner">St Aldric</span><span class="partner">Corvane</span><span class="partner">Fourleigh</span><span class="partner">Dusara Thane</span><span class="partner">Sherwell</span>
</div>

<!-- testimonials -->
<h2 class="abs section-title" style="left:141px;top:2800px">CUSTOMER TESTIMONIALS</h2>
<div class="abs rule" style="left:776px;top:2822px;width:279px"></div>
<svg class="abs" style="left:80px;top:2978px" width="30" height="20" viewBox="0 0 30 20"><path d="M28 7H12V2L2 10l10 8v-5h16z" fill="none" stroke="#333" stroke-width="1.5"/></svg>
<svg class="abs" style="left:1090px;top:2978px" width="30" height="20" viewBox="0 0 30 20"><path d="M2 7h16V2l10 8-10 8v-5H2z" fill="none" stroke="#333" stroke-width="1.5"/></svg>

<div class="abs quote" style="left:131px;top:2916px"><p>" Nemo enim ipsam voluptatem quia voluptas sit aspernatur aut odit aut fugit, sed quia consequuntur magni dolores eos qui ratione voluptatem sequi nesciunt. Neque porro quisquam est, "</p><div class="who">- John Doe</div></div>
<div class="abs quote" style="left:450px;top:2916px"><p>" Nemo enim ipsam voluptatem quia voluptas sit aspernatur aut odit aut fugit, sed quia consequuntur magni dolores eos qui ratione voluptatem sequi nesciunt. Neque porro quisquam est, "</p><div class="who">- John Doe</div></div>
<div class="abs quote" style="left:769px;top:2916px"><p>" Nemo enim ipsam voluptatem quia voluptas sit aspernatur aut odit aut fugit, sed quia consequuntur magni dolores eos qui ratione voluptatem sequi nesciunt. Neque porro quisquam est, "</p><div class="who">- John Doe</div></div>

<div class="abs hex avatar" style="left:332px;top:3018px;background:linear-gradient(#d9b8a0,#8e6b57)" role="img" aria-label="Customer portrait"></div>
<div class="abs hex avatar" style="left:651px;top:3018px;background:linear-gradient(#d98a5a,#b34f2a)" role="img" aria-label="Customer portrait"></div>
<div class="abs hex avatar" style="left:970px;top:3018px;background:linear-gradient(#c9a58e,#5c4638)" role="img" aria-label="Customer portrait"></div>

<div class="abs stars" style="left:131px;top:3077px"><svg width="78" height="14" viewBox="0 0 78 14"><g id="s1"><path d="M7 0l2 5h5l-4 3 2 5-5-3-5 3 2-5-4-3h5z" fill="#f2b51c"/></g><use href="#s1" x="16"/><use href="#s1" x="32"/><path d="M55 0l2 5h5l-4 3 2 5-5-3-5 3 2-5-4-3h5z" fill="#333"/><path d="M71 0l2 5h5l-4 3 2 5-5-3-5 3 2-5-4-3h5z" fill="#333"/></svg></div>
<div class="abs stars" style="left:450px;top:3077px"><svg width="78" height="14" viewBox="0 0 78 14"><use href="#s1"/><use href="#s1" x="16"/><use href="#s1" x="32"/><path d="M55 0l2 5h5l-4 3 2 5-5-3-5 3 2-5-4-3h5z" fill="#333"/><path d="M71 0l2 5h5l-4 3 2 5-5-3-5 3 2-5-4-3h5z" fill="#333"/></svg></div>
<div class="abs stars" style="left:769px;top:3077px"><svg width="78" height="14" viewBox="0 0 78 14"><use href="#s1"/><use href="#s1" x="16"/><use href="#s1" x="32"/><path d="M55 0l2 5h5l-4 3 2 5-5-3-5 3 2-5-4-3h5z" fill="#333"/><path d="M71 0l2 5h5l-4 3 2 5-5-3-5 3 2-5-4-3h5z" fill="#333"/></svg></div>

<!-- newsletter -->
<footer>
  <div class="abs newsletter"></div>
  <h2 class="abs section-title news-title">SIGN UP NEWSLETTER</h2>
  <p class="abs news-text">We treat every customer sincerely and hope we can have the opportunity to Cooperate</p>
  <div class="abs email">Enter Email</div>
  <a class="abs btn subscribe">SUBSCRIBE</a>
  <div class="abs divider"></div>
  <div class="abs pay"><span></span><span></span><span></span><span></span><span></span></div>
  <div class="abs social"><span></span><span></span><span></span><span></span></div>
  <div class="abs footer-nav">HOME &nbsp;/&nbsp; PRODUCTS &nbsp;/&nbsp; PROFILE &nbsp;/&nbsp; CONTACTS &nbsp;/&nbsp; VIDEO &nbsp;/&nbsp; PROMOTION &nbsp;/&nbsp; FEEDS &nbsp;/&nbsp; VIEW MORE</div>
  <div class="abs copy">© 2021 Companyname. All rights reserved. &nbsp;| Privacy Policy &nbsp;| Terms and Use</div>
  <div class="abs foot-brand">Qelmarito</div>
</footer>

</body>
</html>
```